Bright Path Notes Wordpress Blog

I need to design a WordPress blog page. The name of the Blog is "Bright Path Notes". I am hoping for a simple design that is easy for me to post future posts to. I like the color teal for this. The website is brightpathnotesblog.com where I am going to write a personal blog. I don't have a logo for this, but am hoping for a header that has some swirly, but classy looking text. Easy on the eyes. The website will only have a couple of pages - the home landing page, and an about me page.

Font styles to use
Script

Colors
00a990
86cfc6
cfeae6

Requirements
Must have
• A header for the landing page of the blog. Clean layout of where the blog posts will lie.

```html
<!DOCTYPE html>
<html lang="en">
<head>
<meta charset="utf-8">
<title>Bright Path Notes</title>
<link href="https://fonts.googleapis.com/css2?family=Open+Sans:wght@400;600;700&family=Dancing+Script:wght@700&display=swap" rel="stylesheet">
<style>
:root{
  --teal:#00a990;
  --teal-dark:#007f6c;
  --teal-mid:#86cfc6;
  --teal-soft:#cfeae6;
  --ink:#333;
  --muted:#8a8a8a;
  --line:#e4e4e4;
  --page:#f4f6f6;
  --white:#fff;
  --sky-top:#7fb3c0;
  --sky-bottom:#dfecee;
  --ad-yellow:#ffd200;
}
*{box-sizing:border-box;margin:0;padding:0}
html,body{width:1200px;height:3100px;overflow:hidden}
body{position:relative;background:var(--page);font-family:"Open Sans",Arial,sans-serif;color:var(--ink)}
.hero{position:absolute;left:0;top:0;width:1200px;height:660px;background:linear-gradient(180deg,var(--sky-top) 0%,#a9cdd4 45%,var(--sky-bottom) 75%,#c7d6d9 100%)}
.topbar{position:absolute;left:0;top:0;width:1200px;height:74px;background:rgba(10,45,45,.55)}
.brand{position:absolute;left:120px;top:12px;font-family:"Dancing Script",cursive;font-size:38px;font-weight:700;color:var(--white);line-height:48px}
.nav{position:absolute;right:120px;top:28px;display:flex;gap:38px;list-style:none}
.nav li{font-size:15px;font-weight:600;color:var(--white);letter-spacing:.5px}
.hero-title{position:absolute;left:120px;top:380px;width:620px;font-family:"Dancing Script",cursive;font-weight:700;font-size:52px;line-height:62px;color:var(--white)}
.dots{position:absolute;left:570px;top:540px;display:flex;gap:10px}
.dots span{width:10px;height:10px;border-radius:50%;background:rgba(255,255,255,.6)}
.dots span:first-child{background:var(--white)}
.hero-wave{position:absolute;left:0;top:540px}
.post{position:absolute;left:120px;width:608px;height:516px;background:var(--white);border:1px solid var(--line)}
.post-image{height:312px}
.post-title{margin:28px 24px 10px;font-size:22px;font-weight:600;color:var(--ink)}
.post-excerpt{margin:0 24px;font-size:13px;line-height:20px;color:var(--muted)}
.post-meta{position:absolute;left:24px;right:24px;bottom:22px;display:flex;align-items:center}
.read-more{border:1px solid var(--teal);color:var(--teal);font-size:12px;font-weight:700;padding:6px 18px;letter-spacing:.5px}
.comments{margin-left:auto;font-size:12px;color:var(--muted);display:flex;align-items:center;gap:6px}
.comments i{width:14px;height:12px;background:var(--teal-mid);border-radius:3px}
.share{display:flex;gap:4px;margin-left:14px}
.share span{width:18px;height:18px;border-radius:2px;background:var(--teal)}
.share span:nth-child(even){background:var(--teal-mid)}
.widget{position:absolute;left:760px;width:320px;background:var(--white);border:1px solid var(--line)}
.widget-title{text-align:center;font-size:20px;font-weight:700;letter-spacing:1px;padding:22px 0 16px;border-bottom:1px solid var(--line);color:var(--teal)}
.about{top:668px;height:404px;border:none;background:linear-gradient(180deg,var(--teal-mid) 0%,var(--teal) 60%,var(--teal-dark) 100%);color:var(--white);text-align:center}
.about-photo{width:110px;height:110px;border-radius:50%;border:4px solid var(--white);background:var(--teal-soft);margin:36px auto 16px}
.about h3{font-size:22px;font-weight:600;letter-spacing:1px;margin-bottom:14px}
.about p{font-size:12px;line-height:19px;padding:0 40px}
.about .btn{display:inline-block;margin-top:22px;border:1px solid var(--white);padding:7px 20px;font-size:12px;font-weight:700}
.popular{top:1100px;height:460px}
.popular ul{list-style:none;padding:16px 24px}
.popular li{display:flex;gap:14px;margin-bottom:22px}
.popular .thumb{width:90px;height:70px;flex:none}
.popular b{display:block;color:var(--teal);font-size:13px;margin:6px 0 4px}
.popular small{font-size:12px;color:var(--muted)}
.archives{top:1600px;height:420px}
.archives ul{list-style:none;text-align:center;padding-top:14px}
.archives li{font-size:13px;color:var(--muted);line-height:31px}
.recent{top:2048px;height:432px}
.recent .widget-title{color:var(--muted);font-size:17px}
.recent ul{list-style:none;padding:20px 30px}
.recent li{margin-bottom:26px}
.recent b{display:block;color:var(--teal);font-size:14px;font-weight:600;margin-bottom:4px}
.recent small{font-size:12px;color:var(--muted)}
.ad{position:absolute;left:760px;top:2512px;width:320px;height:308px;background:var(--ad-yellow);padding:22px}
.ad-brand{font-size:20px;font-weight:700;color:#222}
.ad-copy{margin-top:20px;width:170px;font-size:22px;font-weight:700;line-height:28px;color:#222}
.ad-device{position:absolute;right:26px;top:70px;width:90px;height:170px;border-radius:10px;background:#e9e9e9;border:3px solid #222}
.pager{position:absolute;left:120px;top:2900px;display:flex;gap:10px}
.pager span{width:34px;height:34px;border-radius:50%;border:1px solid var(--teal);color:var(--teal);font-size:14px;display:flex;align-items:center;justify-content:center}
.pager .active{background:var(--teal);color:var(--white)}
.footer-wave{position:absolute;left:0;top:2960px}
.footer-icons{position:absolute;top:3030px;left:0;width:1200px;display:flex;justify-content:center;gap:12px}
.footer-icons span{width:30px;height:30px;border-radius:50%;border:2px solid var(--white)}
.copyright{position:absolute;top:3072px;width:1200px;text-align:center;font-size:12px;color:var(--white)}
</style>
</head>
<body>

<header class="hero">
  <div class="hero-photo" role="img" aria-label="Hiker with raised arms on a snowy mountain summit under a bright sky" style="position:absolute;inset:0"></div>
  <div class="topbar">
    <div class="brand">Bright Path Notes</div>
    <ul class="nav"><li>HOME</li><li>ABOUT LENA</li><li>CONTACT</li></ul>
  </div>
  <h1 class="hero-title">Help Your to Achive Your Personal Growth &amp; Goals</h1>
  <div class="dots"><span></span><span></span><span></span></div>
</header>
<svg class="hero-wave" width="1200" height="130" viewBox="0 0 1200 130" aria-hidden="true">
  <path d="M0 60 C300 140 800 130 1200 20 L1200 130 L0 130 Z" fill="var(--teal)"/>
  <path d="M0 82 C320 150 820 140 1200 44 L1200 130 L0 130 Z" fill="var(--page)"/>
</svg>

<main>
  <article class="post" style="top:668px">
    <div class="post-image" role="img" aria-label="Climber scaling a rock face" style="background:linear-gradient(160deg,#b9a58c,#6f6556)"></div>
    <h2 class="post-title">Vivamus porttitor purus nisi eleifend libero</h2>
    <p class="post-excerpt">Mauris vel lacus vitae felis vestibulum volutpat. Etiam est nunc venenatis in tristique eu imperdiet ac nisl. Cum sociis natoque penatibus et magnis dis parturient montes nascetur ridiculus mus.</p>
    <div class="post-meta"><span class="read-more">READ MORE</span><span class="comments"><i></i>0 Comments</span><span class="share"><span></span><span></span><span></span><span></span><span></span></span></div>
  </article>
  <article class="post" style="top:1208px">
    <div class="post-image" role="img" aria-label="Businessman with open arms against a sunlit sky" style="background:linear-gradient(160deg,#f3e2b8,#c79a60)"></div>
    <h2 class="post-title">Vivamus porttitor purus nisi eleifend libero</h2>
    <p class="post-excerpt">Mauris vel lacus vitae felis vestibulum volutpat. Etiam est nunc venenatis in tristique eu imperdiet ac nisl. Cum sociis natoque penatibus et magnis dis parturient montes nascetur ridiculus mus.</p>
    <div class="post-meta"><span class="read-more">READ MORE</span><span class="comments"><i></i>0 Comments</span><span class="share"><span></span><span></span><span></span><span></span><span></span></span></div>
  </article>
  <article class="post" style="top:1748px">
    <div class="post-image" role="img" aria-label="Figure at the foot of a tall ladder rising into a cloudy sky" style="background:linear-gradient(180deg,#c9d3dc,#8b9aa6)"></div>
    <h2 class="post-title">Vivamus porttitor purus nisi eleifend libero</h2>
    <p class="post-excerpt">Mauris vel lacus vitae felis vestibulum volutpat. Etiam est nunc venenatis in tristique eu imperdiet ac nisl. Cum sociis natoque penatibus et magnis dis parturient montes nascetur ridiculus mus.</p>
    <div class="post-meta"><span class="read-more">READ MORE</span><span class="comments"><i></i>0 Comments</span><span class="share"><span></span><span></span><span></span><span></span><span></span></span></div>
  </article>
  <article class="post" style="top:2288px">
    <div class="post-image" role="img" aria-label="Hand writing a goals note in a notebook" style="background:linear-gradient(160deg,#d9c7a8,#7d6a55)"></div>
    <h2 class="post-title">Vivamus porttitor purus nisi eleifend libero</h2>
    <p class="post-excerpt">Mauris vel lacus vitae felis vestibulum volutpat. Etiam est nunc venenatis in tristique eu imperdiet ac nisl. Cum sociis natoque penatibus et magnis dis parturient montes nascetur ridiculus mus.</p>
    <div class="post-meta"><span class="read-more">READ MORE</span><span class="comments"><i></i>0 Comments</span><span class="share"><span></span><span></span><span></span><span></span><span></span></span></div>
  </article>

  <nav class="pager"><span>&#8249;</span><span class="active">1</span><span>2</span><span>3</span><span>4</span><span>&#8250;</span></nav>
</main>

<aside>
  <section class="widget about">
    <div class="about-photo" role="img" aria-label="Portrait photo of the blog author"></div>
    <h3>ABOUT LENA</h3>
    <p>Lorem ipsum dolor sit amet, consectetur adipiscing elit. Sed eget tempor mauris, vitae pulvinar lacus. Fusce viverra ut enim sed facilisis, in dictum turpis egestas.</p>
    <span class="btn">READ MORE</span>
  </section>

  <section class="widget popular">
    <h3 class="widget-title">POPULAR</h3>
    <ul>
      <li><span class="thumb" role="img" aria-label="Sunrise landscape" style="background:#d9a86a"></span><div><b>Blog Title Here</b><small>Lorem ipsum dolor sit amet</small></div></li>
      <li><span class="thumb" role="img" aria-label="Person on a hilltop" style="background:#c9b49a"></span><div><b>Blog Title Here</b><small>Lorem ipsum dolor sit amet</small></div></li>
      <li><span class="thumb" role="img" aria-label="City skyline" style="background:#8a9bb0"></span><div><b>Blog Title Here</b><small>Lorem ipsum dolor sit amet</small></div></li>
      <li><span class="thumb" role="img" aria-label="Desk with notebook" style="background:#e2cfc0"></span><div><b>Blog Title Here</b><small>Lorem ipsum dolor sit amet</small></div></li>
    </ul>
  </section>

  <section class="widget archives">
    <h3 class="widget-title">ARCHIVES</h3>
    <ul>
      <li>March 2017</li><li>October 2016</li><li>August 2016</li><li>May 2016</li><li>April 2016</li><li>March 2016</li><li>February 2016</li><li>January 2016</li><li>December 2015</li><li>November 2015</li>
    </ul>
  </section>

  <section class="widget recent">
    <h3 class="widget-title">RECENT COMMENT</h3>
    <ul>
      <li><b>Duis quam libero eget lacus</b><small>sed ut perspiciatis unde omnis</small></li>
      <li><b>Pellentesque habitant</b><small>sed ut perspiciatis unde omnis</small></li>
      <li><b>Aenean porttitor leo</b><small>sed ut perspiciatis unde omnis</small></li>
      <li><b>Nulla rhoncus dictum in</b><small>sed ut perspiciatis unde omnis</small></li>
    </ul>
  </section>

  <section class="ad">
    <div class="ad-brand">Relay Mobile</div>
    <p class="ad-copy">NOW IN WHITE. THE NOVA 4G ONLY FROM RELAY.</p>
    <div class="ad-device" role="img" aria-label="White smartphone product shot"></div>
  </section>
</aside>

<footer>
  <svg class="footer-wave" width="1200" height="140" viewBox="0 0 1200 140" aria-hidden="true">
    <path d="M0 40 C380 -10 820 70 1200 10 L1200 140 L0 140 Z" fill="var(--teal)"/>
    <path d="M0 40 C380 -10 820 70 1200 10" fill="none" stroke="var(--teal-dark)" stroke-width="3"/>
  </svg>
  <div class="footer-icons"><span></span><span></span><span></span><span></span><span></span><span></span></div>
  <p class="copyright">© 2017 Bright Path Notes. All right reserved. Terms of Use</p>
</footer>

</body>
</html>
```